Redesign Comparisson chart - make modern and effective

Use your imaginations to make a powerful distinction between KMV & other holistic modalities. There are 7 elements physical, mental, emotional, energetic, subconscious, superconscious and before and after testing.
We want it to be obvious that KMV is the only modality that works on all these elements simultaneously. We do not want to include any chakras as we want this information to be accepted by a wide range of people and belief systems.'

We want it to look simple but effective. Professional but powerful. We want KMV to stand out even of you eye just passed over i.
Updates

Hi everyone, thanks for your submissions so far. Basically what this image is meant to represent is a comparison chart between all the modalities There are 5 elements physical, mental, emotional, subconscious and superconscious. we want to reflect that KMV is the only modality that works on all these elements simultaneously. As we want the concept to be accepted and not considered woo woo, we want to steer away from chakras.

Target Market(s)

Professionals

Industry/Entity Type

Professional services

Font styles to use
Sans Serif
Other font styles liked:
• Poppins Monserratt

Colors
0094D4
00A9DD
6FCCEA
C7EBF8
E9F6FB

Requirements
Must have
• Clear/professional and clean look. Brand colours and logos. All typography and formats must be cohesive.
Nice to have
• More easy to read, different layout
Should not have
• Do not change the data just the way its presented. No chakras

```html
<!DOCTYPE html>
<html lang="en">
<head>
<meta charset="utf-8">
<title>KMV – Modality Comparison Chart</title>
<link href="https://fonts.googleapis.com/css2?family=Poppins:wght@400;500;600;700&display=swap" rel="stylesheet">
<style>
:root{
  --brand:#2DB8EA;
  --band:#C9ECF9;
  --panel:#E7F5FB;
  --label-bg:#B8DDF3;
  --line:#A6D2EE;
  --line-strong:#2E9BD6;
  --ink:#1A1A1A;
  --physical:#DC4A40;
  --mental:#62BFDC;
  --emotional:#5FAE46;
  --energetic:#F79A23;
  --sub:#EDCB16;
  --super:#8469AD;
  --testing:#D574AA;
}
*{box-sizing:border-box;margin:0;padding:0}
html,body{width:1200px;height:1045px;overflow:hidden;background:#fff}
body{position:relative;font-family:"Poppins",sans-serif;color:var(--ink)}

/* header */
.brand{position:absolute;left:96px;top:22px}
.brand-name{font-size:46px;font-weight:700;color:var(--brand);letter-spacing:1px;line-height:56px}
.headline{position:absolute;left:270px;right:16px;top:20px;text-align:center}
.headline h1{font-size:22.5px;font-weight:600;color:var(--brand);letter-spacing:.2px;line-height:29px}
.headline p{font-size:12.2px;font-weight:500;line-height:17px;margin-top:3px}

/* chart */
.band{position:absolute;left:0;right:0;top:97px;height:762px;background:var(--band)}
.panel{position:absolute;left:291px;top:120px;width:820px;height:718px;background:var(--panel);border-radius:14px 14px 0 0}
.label-col{position:absolute;left:93px;top:177px;width:198px;height:661px;background:var(--label-bg);border-radius:14px 0 0 0}
.chart{position:absolute;left:93px;top:131px;width:1004px}
.row{display:grid;grid-template-columns:198px 110px 109px 110px 110px 119px 119px 129px;position:relative}
.row>div{display:flex;align-items:center;justify-content:center;position:relative;z-index:1}
.row>div+div+div{border-left:1px solid var(--line)}
.row.body{border-bottom:1px solid var(--line)}
.row.body>div:first-child{border-bottom:1px solid #fff;margin-bottom:-1px;justify-content:flex-start;padding-left:14px}
.row.head{height:46px;border-bottom:1px solid var(--line)}
.row.head>div:first-child{border:none}
.row.head>div{font-size:15.5px;font-weight:600;line-height:18px;text-align:center;padding-bottom:6px}
.row.last{border-bottom:none}
.modality{font-size:12.8px;font-weight:500;line-height:14px;list-style:none;white-space:nowrap}
.modality li::before{content:"• "}

.row.kmv{height:43px}
.row.kmv::before{content:"";position:absolute;left:-35px;right:-53px;top:0;bottom:0;background:#fff;border-radius:10px;box-shadow:0 2px 8px rgba(40,90,130,.25)}
.row.kmv>div+div+div{border-left:none;background:linear-gradient(var(--line-strong),var(--line-strong)) no-repeat left center/1px 28px}
.row.kmv>div:first-child{justify-content:flex-start;padding-left:61px;border:none}
.kmv-name{font-size:13px;font-weight:500;line-height:14.5px;letter-spacing:.3px}

.d{width:10px;height:10px;transform:rotate(45deg)}
.kmv .d{width:19px;height:19px}
.p{background:var(--physical)} .m{background:var(--mental)} .e{background:var(--emotional)}
.n{background:var(--energetic)} .s{background:var(--sub)} .u{background:var(--super)} .t{background:var(--testing)}
.c-p{color:var(--physical)} .c-m{color:var(--mental)} .c-e{color:var(--emotional)}
.c-n{color:var(--energetic)} .c-s{color:var(--sub)} .c-u{color:var(--super)} .c-t{color:var(--testing)}

/* legend */
.legend{position:absolute;top:873px;font-size:11px;line-height:13.3px;letter-spacing:-.15px;text-align:justify}
.legend h2{font-size:13.5px;font-weight:600;letter-spacing:0;display:flex;align-items:center;gap:10px;margin-bottom:5px;line-height:16px}
.legend h2 .d{width:9px;height:9px}
.legend h2.gap{margin-top:9px}
.footer-mark{position:absolute;left:99px;top:1010px;display:flex;align-items:center;gap:6px}
.footer-mark .name{font-size:14px;font-weight:600;color:var(--brand)}
.footer-mark .url{font-size:9.5px;font-weight:500;color:var(--brand);border-left:1px solid var(--brand);padding-left:7px;margin-left:4px}
</style>
</head>
<body>

<header>
  <div class="brand"><span class="brand-name">KMV</span></div>
  <div class="headline">
    <h1>CHOOSE KMV FOR FAST, IMMEDIATE AND POWERFUL RESULTS</h1>
    <p>I MUST EXPERIENCE HEALING ON ALL LEVELS, I AM NOT JUST A BODY. I WANT TO LEARN HOW TO HEAL MYSELF, SO I’M NOT DEPENDENT ON OTHERS.<br>I WANT TO RELEASE ALL MY EMOTIONAL AND MENTAL BLOCKS, SO I CAN BE THE BEST VERSION OF MYSELF.</p>
  </div>
</header>

<div class="band"></div>
<div class="panel"></div>
<div class="label-col"></div>

<section class="chart">
  <div class="row head"><div></div>
    <div class="c-p">PHYSICAL</div><div class="c-m">MENTAL</div><div class="c-e">EMOTIONAL</div><div class="c-n">ENERGETIC</div>
    <div class="c-s">SUB<br>CONSCIOUS</div><div class="c-u">SUPER<br>CONSCIOUS</div><div class="c-t">BEFORE &amp;<br>AFTER TESTING</div>
  </div>

  <div class="row body" style="height:80px"><div><ul class="modality"><li>MASSAGE</li><li>YOGA</li><li>NATROPATHY</li><li>AYURVEDIC MEDICINE</li><li>WESTERN MEDICINE</li></ul></div>
    <div><i class="d p"></i></div><div></div><div></div><div></div><div></div><div></div><div></div></div>
  <div class="row body" style="height:29px"><div><ul class="modality"><li>PSYCHIC INTUITIVE</li></ul></div>
    <div><i class="d p"></i></div><div><i class="d m"></i></div><div></div><div></div><div></div><div></div><div></div></div>
  <div class="row body" style="height:30px"><div><ul class="modality"><li>FAMILY CONSTELLATION</li></ul></div>
    <div><i class="d p"></i></div><div><i class="d m"></i></div><div></div><div><i class="d n"></i></div><div></div><div></div><div></div></div>
  <div class="row body" style="height:31px"><div><ul class="modality"><li>ACUPUNCTURE</li></ul></div>
    <div><i class="d p"></i></div><div></div><div></div><div><i class="d n"></i></div><div></div><div></div><div></div></div>
  <div class="row body" style="height:32px"><div><ul class="modality"><li>NUTRITIONAL HEALING</li></ul></div>
    <div><i class="d p"></i></div><div></div><div></div><div></div><div></div><div></div><div><i class="d t"></i></div></div>
  <div class="row body" style="height:32px"><div><ul class="modality"><li>CHINESE MEDICINE</li></ul></div>
    <div><i class="d p"></i></div><div></div><div></div><div><i class="d n"></i></div><div></div><div></div><div><i class="d t"></i></div></div>
  <div class="row body last" style="height:43px"><div><ul class="modality"><li>KINESIOLOGY</li><li>BOWEN THERAPY</li></ul></div>
    <div><i class="d p"></i></div><div></div><div></div><div></div><div><i class="d s"></i></div><div></div><div><i class="d t"></i></div></div>

  <div class="row kmv"><div><span class="kmv-name">KMV<br>HEALING</span></div>
    <div><i class="d p"></i></div><div><i class="d m"></i></div><div><i class="d e"></i></div><div><i class="d n"></i></div>
    <div><i class="d s"></i></div><div><i class="d u"></i></div><div><i class="d t"></i></div></div>

  <div class="row body" style="height:36px"><div><ul class="modality"><li>EFT</li></ul></div>
    <div><i class="d p"></i></div><div><i class="d m"></i></div><div></div><div></div><div><i class="d s"></i></div><div></div><div><i class="d t"></i></div></div>
  <div class="row body" style="height:32px"><div><ul class="modality"><li>CHIROPRACTIC</li></ul></div>
    <div><i class="d p"></i></div><div></div><div></div><div><i class="d n"></i></div><div><i class="d s"></i></div><div></div><div><i class="d t"></i></div></div>
  <div class="row body" style="height:42px"><div><ul class="modality"><li>REIKI</li><li>CRYSTAL HEALING</li></ul></div>
    <div></div><div></div><div></div><div><i class="d n"></i></div><div></div><div></div><div></div></div>
  <div class="row body" style="height:31px"><div><ul class="modality"><li>ENERGY MEDICINE</li></ul></div>
    <div></div><div></div><div></div><div><i class="d n"></i></div><div></div><div></div><div><i class="d t"></i></div></div>
  <div class="row body" style="height:32px"><div><ul class="modality"><li>THETA HEALING</li></ul></div>
    <div></div><div></div><div></div><div></div><div><i class="d s"></i></div><div><i class="d u"></i></div><div></div></div>
  <div class="row body" style="height:32px"><div><ul class="modality"><li>PSYCHOLOGY</li></ul></div>
    <div></div><div><i class="d m"></i></div><div></div><div></div><div></div><div></div><div></div></div>
  <div class="row body" style="height:42px"><div><ul class="modality"><li>MINDFULNESS MEDITATION</li><li>LIFE COACHING</li></ul></div>
    <div></div><div><i class="d m"></i></div><div></div><div></div><div></div><div></div><div><i class="d t"></i></div></div>
  <div class="row body" style="height:42px"><div><ul class="modality"><li>HYPNOTHERAPY</li><li>INNER CHILD HEALING</li></ul></div>
    <div></div><div><i class="d m"></i></div><div></div><div></div><div><i class="d s"></i></div><div></div><div></div></div>
  <div class="row body last" style="height:38px"><div><ul class="modality"><li>NLP</li><li>TIMELINE THERAPY</li></ul></div>
    <div></div><div><i class="d m"></i></div><div></div><div></div><div><i class="d s"></i></div><div></div><div><i class="d t"></i></div></div>
</section>

<section class="legend" style="left:93px;width:221px">
  <h2 class="c-p"><i class="d p"></i>PHYSICAL</h2>
  <p>Most modalities, including, a western medicine, focus on and treat the physical body only. The KMV process enables you to engage in healing your own body during the session. There is no muscle testing, no hands-on healing and no herbal remedies or medicines.</p>
</section>
<section class="legend" style="left:340px;width:218px">
  <h2 class="c-m"><i class="d m"></i>MENTAL</h2>
  <p>KMV enables you to use your own consciousness to self-heal. We don’t give you advice or coaching, we allow your mind to heal itself.</p>
  <h2 class="c-n gap"><i class="d n"></i>ENERGETIC</h2>
  <p>Most modalities try to move the energy in your body for you. KMV enables and empowers you to do it yourself.</p>
</section>
<section class="legend" style="left:584px;width:268px">
  <h2 class="c-e"><i class="d e"></i>EMOTIONAL</h2>
  <p>KMV is the only modality that engages your emotions on a physical level. Emotions get stuck in your body and can cause illness over time if left unchecked. KMV enables you you experience fast and powerful emotional releasing</p>
  <h2 class="c-u gap"><i class="d u"></i>SUPERCONSCIOUS</h2>
  <p>KMV is the only modality the enables you to access and heal your superconscious mind yourself.</p>
</section>
<section class="legend" style="left:877px;width:233px;top:872px">
  <h2 class="c-s"><i class="d s"></i>SUBCONSCIOUS</h2>
  <p>Some modalities, like Kinesiology, access your subconscious through muscle testing. KMV empowers you to access your own subconscious and heal it yourself.</p>
  <h2 class="c-t gap"><i class="d t"></i>BEFORE &amp; AFTER TESTING</h2>
  <p>KMV is the only modality the enables you to provide before and after results, which are documented by us, and analysed by you with our help.</p>
</section>

<footer class="footer-mark"><span class="name">Lumenwell</span><span class="url">www.lumenwell.com.au</span></footer>

</body>
</html>
```